Luxury Real Estate Website, Midwest, United States

We need web design services for a luxury website. We need IDX Integration with our MLS. We want this to be a very simple website with amazing graphics. We want it to link up with our MailChimp account in order to generate leads through a "More Information" Pop up on the main page. We want the main page to be covered with one large graphic that is a rolling slideshow of active listings of $400,000 and up from the IDX Integration. We need this website to give a very exclusive and sleek look. Lots of black is good... I will upload our logos in Black and Silver. We will also need an "About" page that we are going to call "Qeno Info". We want our graphics to be extremely impressive. Keep in mind, we are a company in the Midwest of the United States, and our real estate has a different look than homes in California or Florida. We need graphics that are realistic for the Midwest, yet still high-end.
Target Market(s)
Luxury Homeowners in the Midwest United States. The graphics needs to be pristine.
Industry/Entity Type
Real Estate
Coding
Coded - Design and coding required
Number of Pages Required
3 page
Requirements
Must have
- Large graphics with IDX Integration. The photos of real estate need to represent real estate that is common in the Midwest, United States. We also need MailChimp integration. We need a pop up that is titled "My Free Market Analysis" that makes them fill out a contact form asking for Full Name, Email Address, Phone Number and Address. This needs to be a pop up on the front page and will integrate with our MailChimp account. We also need a page called "About Qe No Home". And another page where clients can download informational PDFs. The main component needs to be a front page search engine connected with the IDX to access active listings from our MLS. I attached our logos and a sample front page of a website. I would love for ours to look similar.
Nice to have
- Lake House photos on midwest lakes are a plus.
Should not have
- Should not have clutter. This website needs to be clean, luxurious and exclusive.

```html
<!DOCTYPE html>
<html lang="en">
<head>
<meta charset="utf-8">
<title>Harbor Crest Realty Group</title>
<link href="https://fonts.googleapis.com/css2?family=Poppins:wght@300;400;500&family=Open+Sans:wght@400;600&family=Lora:ital@1&display=swap" rel="stylesheet">
<style>
:root{
  --ink:#333333;
  --muted:#5a5a5a;
  --soft-bg:#f3f3f3;
  --white:#ffffff;
  --accent:#8fadd6;
  --accent-btn:#94b0d6;
  --tagline:#7f9fcc;
  --footer:#1f1f1f;
  --footer-line:#3a3a3a;
  --panel:rgba(20,20,20,.78);
}
*{margin:0;padding:0;box-sizing:border-box}
html,body{width:1200px;height:2553px;overflow:hidden}
body{font-family:"Open Sans",Arial,sans-serif;color:var(--ink);background:var(--white);position:relative}
.abs{position:absolute}

/* header */
.site-header{position:absolute;left:0;top:0;width:1200px;height:106px;background:var(--white)}
.brand{position:absolute;left:88px;top:30px;display:flex;align-items:center;gap:12px;font-family:"Poppins",sans-serif;font-weight:400;font-size:24px;color:#111;letter-spacing:.5px}
.brand-mark{width:14px;height:14px;background:#111}
.main-nav{position:absolute;top:44px;left:0;width:1200px;font-family:"Poppins",sans-serif;font-size:13px;color:#444;letter-spacing:.3px}
.main-nav a{position:absolute;color:inherit;text-decoration:none;white-space:nowrap}

/* hero */
.hero{position:absolute;left:0;top:106px;width:1200px;height:544px;background:linear-gradient(180deg,#c9d6e3 0%,#d9cfb6 28%,#b69c78 48%,#6f8f4c 72%,#4f7a35 90%,#5d7285 100%)}
.search-panel{position:absolute;left:260px;top:253px;width:681px;height:126px;background:var(--panel)}
.search-title{position:absolute;left:24px;top:16px;font-family:"Poppins",sans-serif;font-size:21px;color:var(--white);font-weight:400}
.search-input{position:absolute;left:23px;top:55px;width:580px;height:44px;background:var(--white);font-size:12px;color:#555;padding:14px 15px}
.search-btn{position:absolute;left:603px;top:55px;width:56px;height:44px;background:#bccbdc;display:flex;align-items:center;justify-content:center}

/* welcome */
.welcome{position:absolute;left:0;top:650px;width:1200px;height:814px;background:var(--soft-bg)}
.photo-lake{position:absolute;left:0;top:0;width:536px;height:439px;background:linear-gradient(160deg,#6fa3d8 0%,#9bb4c4 35%,#5b6a4b 60%,#3f6f9e 100%)}
.photo-porch{position:absolute;left:311px;top:279px;width:285px;height:240px;background:linear-gradient(135deg,#5f8fc4 0%,#b9a27a 45%,#a5282b 75%,#7a5b3a 100%)}
.welcome-copy{position:absolute;left:688px;top:58px;width:400px}
.welcome-kicker{font-family:"Poppins",sans-serif;font-weight:300;font-size:25px;color:#555;line-height:1}
.welcome-title{font-family:"Poppins",sans-serif;font-weight:400;font-size:33px;color:#333;margin-top:14px;line-height:1.1;white-space:nowrap}
.welcome-tagline{font-family:"Lora",serif;font-style:italic;font-size:15px;color:var(--tagline);margin-top:22px}
.welcome-text{font-size:11.5px;line-height:25.5px;color:var(--muted);margin-top:15px}
.welcome-text + .welcome-text{margin-top:25px}
.btn-outline{position:absolute;left:691px;top:458px;width:189px;height:44px;border:2px solid #888;font-size:13.5px;color:#444;display:flex;align-items:center;justify-content:center;background:transparent}
.feature{position:absolute;top:600px;width:340px;text-align:center}
.feature svg{display:block;margin:0 auto}
.feature-title{font-family:"Poppins",sans-serif;font-size:16px;color:#555;margin-top:14px}
.feature-text{font-size:11.5px;line-height:27px;color:var(--muted);margin-top:4px}

/* featured */
.featured{position:absolute;left:0;top:1464px;width:1200px;height:594px;background:var(--white)}
.section-title{position:absolute;top:42px;width:1200px;text-align:center;font-family:"Poppins",sans-serif;font-weight:500;font-size:26px;color:#333;letter-spacing:.5px}
.section-sub{position:absolute;top:86px;width:1200px;text-align:center;font-size:11.5px;color:var(--muted)}
.card{position:absolute;top:131px;width:329px;height:417px;border:1px solid #dedede;background:var(--white)}
.card-photo{position:absolute;left:7px;top:7px;width:313px;height:197px}
.card-title{position:absolute;top:226px;width:100%;text-align:center;font-family:"Poppins",sans-serif;font-size:17px;color:#333}
.card-text{position:absolute;left:20px;top:263px;width:287px;text-align:center;font-size:11.5px;line-height:25.5px;color:var(--muted)}
.btn-fill{position:absolute;left:108px;top:358px;width:112px;height:37px;background:var(--accent-btn);color:var(--white);font-size:13.5px;display:flex;align-items:center;justify-content:center}

/* call to action */
.cta-band{position:absolute;left:0;top:2058px;width:1200px;height:246px;background:var(--accent);text-align:center;color:var(--white)}
.cta-title{position:absolute;top:60px;width:1200px;font-family:"Poppins",sans-serif;font-size:21px;letter-spacing:.6px}
.cta-sub{position:absolute;top:102px;width:1200px;font-family:"Poppins",sans-serif;font-weight:300;font-size:18px}
.btn-ghost{position:absolute;left:495px;top:155px;width:210px;height:47px;border:1px solid var(--white);font-family:"Poppins",sans-serif;font-size:17px;display:flex;align-items:center;justify-content:center}

/* footer */
.site-footer{position:absolute;left:0;top:2304px;width:1200px;height:249px;background:var(--footer);color:var(--white)}
.footer-brand{position:absolute;left:145px;top:86px;display:flex;align-items:center;gap:12px;font-family:"Poppins",sans-serif;font-size:27px;letter-spacing:.5px}
.footer-brand .brand-mark{background:var(--white)}
.footer-heading{position:absolute;top:26px;font-family:"Poppins",sans-serif;font-weight:500;font-size:15px;letter-spacing:.5px}
.footer-link{position:absolute;font-size:11.5px;white-space:nowrap}
.newsletter-text{position:absolute;left:763px;top:72px;font-size:11.5px}
.newsletter-form{position:absolute;left:764px;top:108px;width:337px;height:44px;background:var(--white)}
.newsletter-input{position:absolute;left:18px;top:14px;font-size:11.5px;color:#555}
.newsletter-btn{position:absolute;right:0;top:0;width:45px;height:44px;background:#bccbdc;display:flex;align-items:center;justify-content:center}
.footer-rule{position:absolute;left:85px;top:181px;width:1030px;height:1px;background:var(--footer-line)}
.copyright{position:absolute;top:208px;width:1200px;text-align:center;font-size:11px}
</style>
</head>
<body>

<header class="site-header">
  <div class="brand"><span class="brand-mark"></span>Harbor Crest</div>
  <nav class="main-nav">
    <a style="left:520px">HOME</a>
    <a style="left:606px">QENO INFO</a>
    <a style="left:722px">ABOUT QE NO HOME</a>
    <a style="left:898px">DOWNLOADS</a>
    <a style="left:1030px">CONTACT US</a>
  </nav>
</header>

<section class="hero" role="img" aria-label="Lakefront luxury homes with green lawns under a cloudy sky">
  <div class="search-panel">
    <div class="search-title">Harbor Crest Realty</div>
    <div class="search-input">Enter Your Keyword ....</div>
    <div class="search-btn">
      <svg width="18" height="18" viewBox="0 0 18 18" fill="none" stroke="#ffffff" stroke-width="2"><circle cx="7.5" cy="7.5" r="5.5"/><line x1="11.5" y1="11.5" x2="16" y2="16"/></svg>
    </div>
  </div>
</section>

<section class="welcome">
  <div class="photo-lake" role="img" aria-label="Lakeside homes with boat docks along a canal"></div>
  <div class="photo-porch" role="img" aria-label="Family relaxing on the deck of a red lake cottage"></div>
  <div class="welcome-copy">
    <div class="welcome-kicker">Welcome to</div>
    <div class="welcome-title">HARBOR CREST REALTY GROUP</div>
    <div class="welcome-tagline">A luxury real estate company from Midwest, United states</div>
    <p class="welcome-text">Sed ut perspiciatis unde omnis iste natus error sit voluptatem accusanti um doloremque laudantium, totam rem aperiam, eaque ipsa quae ab illo inventore veritatis et quasi architecto beatae vitae dicta sunt explicabo. Nemo enim ipsam voluptatem quia voluptas sit aspernatur</p>
    <p class="welcome-text">Sed ut perspiciatis unde omnis iste natus error sit voluptatem accusanti um doloremque laudantium, totam rem aperiam, eaque ipsa quae ab illo inventore veritatis et quasi architecto beatae vitae dicta sunt explicabo. Nemo enim ipsam voluptatem quia voluptas sit aspernatur</p>
  </div>
  <div class="btn-outline">Click Here For More Info</div>

  <div class="feature" style="left:73px">
    <svg width="60" height="54" viewBox="0 0 60 54" fill="none" stroke="#555" stroke-width="2"><path d="M12 24 L30 8 L48 24"/><rect x="16" y="22" width="28" height="20"/><rect x="25" y="29" width="10" height="13"/><line x1="4" y1="46" x2="56" y2="46"/><line x1="8" y1="51" x2="52" y2="51"/></svg>
    <div class="feature-title">Contrary to Popular</div>
    <div class="feature-text">Sed ut perspiciatis unde omnis iste natus error sit<br>voluptatem accusanti um doloremque</div>
  </div>
  <div class="feature" style="left:422px">
    <svg width="60" height="60" viewBox="0 0 60 60" fill="none" stroke="#555" stroke-width="2"><path d="M20 4 C16 12 12 17 12 22 a8 8 0 0 0 16 0 C28 17 24 12 20 4 Z"/><path d="M6 38 q6-5 12 0 t12 0 t12 0 t12 0"/><path d="M6 46 q6-5 12 0 t12 0 t12 0 t12 0"/><path d="M6 54 q6-5 12 0 t12 0 t12 0 t12 0"/></svg>
    <div class="feature-title">Contrary to Popular</div>
    <div class="feature-text">Sed ut perspiciatis unde omnis iste natus error sit<br>voluptatem accusanti um doloremque</div>
  </div>
  <div class="feature" style="left:771px">
    <svg width="66" height="62" viewBox="0 0 66 62" fill="#555"><path d="M30 18 L48 2 L66 18 L62 18 L62 34 L50 34 L50 24 L44 24 L44 30 L34 30 L34 18 Z"/><circle cx="24" cy="30" r="9"/><path d="M6 60 C6 46 14 42 24 42 C34 42 42 46 42 60 Z"/></svg>
    <div class="feature-title">Contrary to Popular</div>
    <div class="feature-text">Sed ut perspiciatis unde omnis iste natus error sit<br>voluptatem accusanti um doloremque</div>
  </div>
</section>

<section class="featured">
  <h2 class="section-title">OUR FEATURED PROPERTY</h2>
  <p class="section-sub">Sed ut perspiciatis unde omnis iste natus error sit voluptatem accusanti um doloremque laudantium, totam rem aperiam,</p>

  <article class="card" style="left:85px">
    <div class="card-photo" role="img" aria-label="Wooden lake house among pine trees on a rocky shore" style="background:linear-gradient(180deg,#6f9fd6 0%,#3f6a3a 45%,#8a6a4e 75%,#3d5f7c 100%)"></div>
    <h3 class="card-title">Sed ut perspiciatis unde</h3>
    <p class="card-text">Nemo enim ipsam voluptatem quia voluptas sit asper-natur aut odit aut fugit, sed quia consequuntur magni ratione voluptatem sequi nesciunt.</p>
    <div class="btn-fill">Read More</div>
  </article>
  <article class="card" style="left:436px">
    <div class="card-photo" role="img" aria-label="Large white two-story home beside a pond" style="background:linear-gradient(180deg,#3f86d4 0%,#dfe4ea 40%,#5f8a3f 75%,#2f5f4f 100%)"></div>
    <h3 class="card-title">Sed ut perspiciatis unde</h3>
    <p class="card-text">Nemo enim ipsam voluptatem quia voluptas sit asper-natur aut odit aut fugit, sed quia consequuntur magni ratione voluptatem sequi nesciunt.</p>
    <div class="btn-fill">Read More</div>
  </article>
  <article class="card" style="left:785px">
    <div class="card-photo" role="img" aria-label="Red-roofed lake cottage with a deck among tall trees" style="background:linear-gradient(180deg,#2f4a2a 0%,#a5402e 38%,#5a4a36 65%,#b59a72 100%)"></div>
    <h3 class="card-title">Sed ut perspiciatis unde</h3>
    <p class="card-text">Nemo enim ipsam voluptatem quia voluptas sit asper-natur aut odit aut fugit, sed quia consequuntur magni ratione voluptatem sequi nesciunt.</p>
    <div class="btn-fill">Read More</div>
  </article>
</section>

<section class="cta-band">
  <div class="cta-title">SED UT PERSPICIATIS UNDE OMNIS ISTE NATUS ERROR SIT VOLUPTATEM</div>
  <div class="cta-sub">accusantium doloremque laudantium, totam rem aperiam</div>
  <div class="btn-ghost">Downloads</div>
</section>

<footer class="site-footer">
  <div class="footer-brand"><span class="brand-mark"></span>Harbor Crest</div>

  <div class="footer-heading" style="left:454px">QUICK LINKS</div>
  <span class="footer-link" style="left:455px;top:72px">Home</span>
  <span class="footer-link" style="left:455px;top:101px">Qeno Info</span>
  <span class="footer-link" style="left:455px;top:130px">About Qe No Home</span>
  <span class="footer-link" style="left:613px;top:72px">Downloads</span>
  <span class="footer-link" style="left:613px;top:101px">Contact us</span>

  <div class="footer-heading" style="left:763px">NEWSLETTER</div>
  <div class="newsletter-text">Sed ut perspiciatis unde omnis iste natus error sit</div>
  <div class="newsletter-form">
    <span class="newsletter-input">Enter Your Email Id :</span>
    <div class="newsletter-btn">
      <svg width="18" height="18" viewBox="0 0 18 18" fill="#ffffff"><path d="M1 8 L17 1 L12 17 L9 10 Z"/></svg>
    </div>
  </div>

  <div class="footer-rule"></div>
  <div class="copyright">© Copy Right -2018 Harbor Crest Realty Group.All rights reserved.</div>
</footer>

</body>
</html>
```